Northfield Builders Guild Business card

We are looking for a new business card design with photo included.
Our business is a nonprofit construction contractor membership organization. We offer business education, assist with business setup and licensing, provide safety training, and provide a member directory.
URL: www.builderslinkguild.org
Color code:
CMYK: 0 cyan, 42 magenta, 100 yellow, 0 black for Print.
Hexidecimal: #FF9900
RGB: R 255; G 153; B 0

```html
<!DOCTYPE html>
<html lang="en">
<head>
<meta charset="utf-8">
<title>Northfield Builders Guild – Business Card</title>
<link href="https://fonts.googleapis.com/css2?family=Open+Sans:wght@400;600;700;800&display=swap" rel="stylesheet">
<style>
  :root {
    --backdrop: #dcdcda;
    --card: #333335;
    --card-deep: #2a2a2c;
    --accent: #ff9900;
    --ink-light: #ffffff;
    --ink-soft: #e6e6e6;
  }
  * { box-sizing: border-box; margin: 0; padding: 0; }
  html, body {
    width: 1200px; height: 801px; overflow: hidden;
    background: var(--backdrop);
    font-family: "Open Sans", Arial, sans-serif;
  }
  .stage { position: relative; width: 1200px; height: 801px; }
  .card {
    position: absolute; top: 252px;
    width: 520px; height: 297px;
    background: var(--card);
    border-bottom: 3px solid var(--accent);
    border-right: 2px solid var(--accent);
  }
  .card--front { left: 50px; }
  .card--back { left: 630px; }

  .brand {
    position: absolute; left: 34px; top: 96px; width: 210px;
    color: var(--ink-light);
    font-weight: 800; font-size: 31px; line-height: 1.02;
    text-transform: uppercase; letter-spacing: -0.5px;
  }
  .divider {
    position: absolute; left: 262px; top: 62px;
    width: 1px; height: 172px; background: var(--accent);
  }
  .contact {
    position: absolute; left: 282px; top: 62px;
    color: var(--ink-soft); font-size: 12.5px; line-height: 19px;
  }
  .contact__name {
    color: var(--accent); font-weight: 700; font-size: 19px;
    line-height: 24px; text-transform: uppercase;
  }
  .contact__role { margin-bottom: 2px; }
  .contact__line { display: flex; align-items: center; gap: 6px; }
  .contact__line svg { width: 11px; height: 11px; flex: none; }

  .back-mark {
    position: absolute; left: 0; right: 0; top: 128px;
    text-align: center;
    color: var(--card-deep);
    font-weight: 800; font-size: 34px; text-transform: uppercase;
    letter-spacing: -0.5px;
  }
</style>
</head>
<body>
<main class="stage">
  <section class="card card--front">
    <div class="brand">Northfield<br>Builders<br>Guild</div>
    <div class="divider"></div>
    <div class="contact">
      <p class="contact__name">Dale Harwick</p>
      <p class="contact__role">President</p>
      <p>4820 Ridgeline Ave., Suite #210</p>
      <p>Millbrook, OR 97402</p>
      <p class="contact__line">
        <svg viewBox="0 0 12 12" aria-hidden="true"><circle cx="6" cy="6" r="6" fill="#ff9900"/><path d="M3.6 3.2l1.3-.4.7 1.6-.8.6c.4.8 1 1.4 1.8 1.8l.6-.8 1.6.7-.4 1.3C6 8 4 6 3.6 3.2z" fill="#333335"/></svg>
        (555) 310-2874
      </p>
      <p class="contact__line">
        <svg viewBox="0 0 12 12" aria-hidden="true"><circle cx="6" cy="6" r="6" fill="#ff9900"/><rect x="3" y="4" width="6" height="4.2" fill="#333335"/><path d="M3 4l3 2.3L9 4" stroke="#ff9900" stroke-width=".7" fill="none"/></svg>
        support@nfbguild.org
      </p>
      <p class="contact__line">
        <svg viewBox="0 0 12 12" aria-hidden="true"><circle cx="6" cy="6" r="6" fill="#ff9900"/><circle cx="6" cy="6" r="3" fill="none" stroke="#333335" stroke-width=".8"/><path d="M3 6h6M6 3v6" stroke="#333335" stroke-width=".7"/></svg>
        www.builderslinkguild.org
      </p>
    </div>
  </section>

  <section class="card card--back">
    <p class="back-mark">Northfield Builders Guild</p>
  </section>
</main>
</body>
</html>
```